Wordpress Theme for Medical Clinics

** Please view updated Sitemap2.pdf doc to clarify some confusion ***

This is a multiuser WordPress subscription site for medical clinics. Please see attachment for sitemap. Please do not include extra content like social media icons, search bars, or images. If you have questions, please ask for clarification.
The site contains the following pages and sub-pages:

1. Home
2. Our Clinic
2a. Our Clinic > Mission
2b. Our Clinic > Services
2c. Our Clinic > Clinic Policies
2d. Our Clinic > Schedules
3. Our Staff
3a. Our Staff > [Staff member page]
4. Resources
4a. Resources > Patient Health (index)
4b. Resources > Patient Health (index) > [post]
4c. Resources > Links
4d. Resources > Forms
5. Alerts
5a. Alerts > [Alert Page]
6. Contact Us

Includes the Following Pages, Subpages, and Content
1. Home
a. About Us
b. Our Staff
c. Bulletins
d. Accepting New Patients (shown as an alert widget)
e. Links
i. Physician Toolbox
ii. Book an Appointment
f. Clinic Policies
i. Show first 3 policies (e.g. Late Arrivals, Missed Appointments, Fees)
ii. Link to Clinic Policies page
g. Primary widget (displayed on all pages)
i. Hours of operation
ii. Contact Info
1. Tel
2. Fax
3. Email
4. Address
5. Get directions (link to Google Maps)
2. Our Clinic
a. Main Page
i. Clinic Name
ii. Overview
iii. Languages Spoken
iv. Secondary Navigation
1. Mission
2. Services
3. Clinic Policies
4. Schedules (see attachment)
b. Our Clinic > Mission
c. Our Clinic > Services
i. For each service include service TITLE and DESCRIPTION
d. Our Clinic > Clinic Policies
i. For each policy include policy TITLE and DESCRIPTION
ii. Include the following policies in mockup
1. Late arrivals
2. Missed appointments
3. Fees for missed appointments
4. Referrals and follow-ups
5. Services not covered by RDA
6. Information for LTF patients
7. Medical Legal Reports
e. Our Clinic > Schedules
3. Our Staff
a. Main Page
i. Display a list of staff members. Include NAME and DESIGNATION
b. Our Staff > [Staff Name]
i. Include NAME, PICTURE, DESIGNATION, and BIO
4. Resources
a. Resources > Patient Health
i. Main Page
1. Posts (ordered by date)
a. Title
b. Summary
2. Side Navigation
a. Post Categories
ii. Patient Health > [post title]
1. Title
2. Post Category
3. Date
4. Author
5. Summary
6. Body
b. Resources > Links
1. Secondary Navigation - Categories
a. Sample Categories:
i. Local Services
ii. RDA and Drug Coverage
iii. Mental Health Resources
2. Category page
a. Include the following links in the 'Local Services' category
i. Hypertension clinics
ii. Home Care services
iii. Vaccine Clinics
c. Resources > Forms
i. Display a table with form TITLE and CATEGORY
ii. Side Navigation
1. Form Categories
a. Use the following sample Categories
i. Referrals
ii. Insurance
iii. Intake
iv. Discharge
v. Waivers
5. Alerts
a. Main page
i. List of all Alert posts
1. Include post TITLE as a link to the post
ii. Side Navigation
1. Alerts Archive
a. shown as Month + Number of posts
iii. Alerts > [Alert page]
1. Include TITLE, DATE, AUTHOR, BODY
6. Contact Us
a. Map
b. Hours of operation
c. Address
d. Phone number
e. Fax number
e. Fax number
f. Map
g. Email

Design notes:
- fixed width
- responsive (need designs for mobile, tablet, and desktop)
- simple, dark font, white background
- use Font Awesome icons where needed
- user adds own logo

Target Market(s)

Medical Clinics

Industry/Entity Type

Medical

Number of Pages Required

5+ page

Font styles to use
Serif
Sans Serif

Requirements
Must have
• Please keep designs very simple.
• Examples:
• https://www.quolbin.com/install
• http://www.ventrohax.com/company/about-us
• http://brindlequota.org/
• http://www.trosk.com/
Should not have
• Minimal or no use of shadows and gradients

```html
<!DOCTYPE html>
<html lang="en">
<head>
<meta charset="utf-8">
<title>Medical – Contact Us</title>
<link href="https://fonts.googleapis.com/css2?family=Open+Sans:wght@300;400;600;700&display=swap" rel="stylesheet">
<style>
:root{
  --blue:#1a7cc9;
  --blue-light:#8ec5ea;
  --text:#333;
  --muted:#7a7a7a;
  --line:#e2e2e2;
  --outer:#ececec;
  --footer:#333436;
  --footer-bottom:#2a2b2d;
  --footer-text:#c9c9c9;
  --map-land:#e9e5dc;
  --map-water:#a9c4e4;
}
*{box-sizing:border-box;margin:0;padding:0}
html,body{width:1000px;height:1200px;overflow:hidden}
body{background:var(--outer);font-family:"Open Sans",Arial,sans-serif;color:var(--text);position:relative}
.page{position:absolute;left:50px;top:0;width:900px;height:1200px;background:#fff}
.abs{position:absolute}
a{color:inherit;text-decoration:none}
svg.ico{display:inline-block;vertical-align:middle}

/* top bar */
.topbar{left:0;top:0;width:900px;height:24px;border-top:2px solid var(--blue-light);border-bottom:1px solid var(--line);font-size:8px;color:var(--muted)}
.topbar .call{left:65px;top:6px}
.topbar .call b{font-weight:600;color:#555}
.topbar .links{right:66px;top:5px;display:flex;gap:12px;align-items:center}
.topbar .links span{display:flex;align-items:center;gap:4px}

/* header */
.brand{left:65px;top:37px;display:flex;align-items:center;gap:8px;font-size:20px;color:#222}
.brand .dot{width:32px;height:32px;border-radius:50%;background:var(--blue)}
.nav{right:64px;top:46px;display:flex;gap:22px;font-size:11px;color:#333}
.nav .active{color:var(--blue);position:relative}
.nav .active::before{content:"";position:absolute;left:0;right:0;top:-21px;height:2px;background:var(--blue)}

/* title band */
.band{left:0;top:88px;width:900px;height:58px;background:linear-gradient(#f3f3f3,#fff)}
.page-title{left:65px;top:105px;font-size:17px;color:var(--blue);font-weight:400}
.title-rule{left:65px;top:140px;width:770px;height:1px;background:var(--line)}
.title-accent{left:65px;top:139px;width:59px;height:2px;background:var(--blue)}
.crumbs{left:164px;top:112px;font-size:8px;color:#666}
.crumbs a{text-decoration:underline}
.directions{left:585px;top:103px;width:251px;height:24px;display:flex}
.directions .field{flex:1;border:1px solid var(--line);font-size:8px;color:#aaa;padding:6px 8px;background:#fff}
.directions .go{width:25px;background:var(--blue);display:flex;align-items:center;justify-content:center}

/* map */
.map{left:65px;top:162px;width:770px;height:258px;background:linear-gradient(100deg,var(--map-land) 0%,#e4e3d4 55%,#dfe2e0 75%,var(--map-water) 100%);box-shadow:0 8px 14px -6px rgba(0,0,0,.25)}

/* form */
.h2{font-size:24px;font-weight:300;color:#222}
.form-title{left:66px;top:479px}
.input{border:1px solid var(--line);box-shadow:inset 0 0 0 2px #f6f6f6;font-size:8px;font-weight:600;color:#777;padding:9px 8px}
.input i{color:var(--blue);font-style:normal}
.f1{left:65px;top:530px;width:246px;height:28px}
.f2{left:324px;top:530px;width:247px;height:28px}
.f3{left:65px;top:571px;width:246px;height:28px}
.f4{left:324px;top:571px;width:247px;height:28px}
.f5{left:65px;top:612px;width:506px;height:120px}
.send{left:489px;top:743px;width:82px;height:28px;background:var(--blue);color:#fff;font-size:9px;display:flex;align-items:center;justify-content:center;gap:6px}

/* contact */
.contact-title{left:591px;top:479px}
.contact-list{left:592px;top:530px;width:244px}
.contact-list li{list-style:none;border-top:1px solid var(--line);display:flex;gap:10px;font-size:8.5px;color:#666;line-height:15px;padding:10px 0 11px 6px}
.contact-list li b{color:#222}
.contact-list li a{color:var(--blue)}
.contact-list li:last-child{padding-bottom:0}

/* footer */
.footer{left:0;top:861px;width:900px;height:288px;background:var(--footer);color:var(--footer-text);font-size:8.5px;line-height:15px}
.footer .brand{color:#fff;top:39px}
.footer .brand .dot{width:30px;height:30px}
.f-col{position:absolute;top:48px}
.f-col h4{color:#fff;font-size:9px;font-weight:600;margin-bottom:22px}
.about{left:65px;top:84px;width:150px}
.f-contact{left:65px;top:130px;width:170px}
.f-row{display:flex;gap:10px;margin-bottom:14px}
.f-row b{color:#fff;font-weight:600}
.clinic-links{left:256px}
.clinic-links li{list-style:none;color:#fff;display:flex;gap:8px;align-items:center;margin-bottom:5px}
.resources{left:450px;width:170px}
.res-item{display:flex;gap:6px;margin-bottom:22px}
.res-item b{color:#fff;font-weight:600}
.res-item .ago{display:block;color:var(--blue-light);font-size:7px;margin-top:2px}
.news{left:643px;width:180px}
.subscribe{display:flex;margin-top:14px;height:20px}
.subscribe .field{width:118px;background:#eee;color:#999;font-size:8px;padding:3px 8px}
.subscribe .btn{width:58px;background:var(--blue);color:#fff;font-size:8px;display:flex;align-items:center;justify-content:center}
.footer-bottom{left:0;top:1149px;width:900px;height:51px;background:var(--footer-bottom);color:var(--footer-text);font-size:7.5px;padding:19px 65px}
</style>
</head>
<body>
<div class="page">

  <div class="abs topbar">
    <div class="abs call"><b>Call Us Today!</b>&nbsp; +123 480 210 &nbsp;&nbsp;|&nbsp;&nbsp; hello@clinicmail.com</div>
    <div class="abs links">
      <span><svg class="ico" width="10" height="11" viewBox="0 0 10 11"><rect x="1" y="1.5" width="8" height="9" fill="none" stroke="#999"/><rect x="3" y="0" width="4" height="3" fill="#999"/></svg>Book an Appointment</span>
      <span>|</span>
      <span><svg class="ico" width="12" height="10" viewBox="0 0 12 10"><rect x="0.5" y="2.5" width="11" height="7" fill="none" stroke="#999"/><rect x="4" y="0.5" width="4" height="2" fill="none" stroke="#999"/><path d="M6 4v4M4 6h4" stroke="#999"/></svg>Physician Toolbox</span>
    </div>
  </div>

  <div class="abs brand"><span class="dot"></span>Medical</div>
  <nav class="abs nav">
    <a href="#">Home</a><a href="#">Our Clinic</a><a href="#">Staff</a><a href="#">Resources</a><a href="#">Alerts</a><a href="#" class="active">Contact</a>
  </nav>

  <div class="abs band"></div>
  <h1 class="abs page-title">Contact Us</h1>
  <div class="abs crumbs"><a href="#">Home</a> &nbsp;›&nbsp; Contact Us</div>
  <div class="abs title-rule"></div>
  <div class="abs title-accent"></div>
  <div class="abs directions">
    <div class="field">Please enter your starting location to get directions</div>
    <div class="go"><svg width="8" height="8" viewBox="0 0 8 8"><path d="M1 1l3 3-3 3M4 1l3 3-3 3" fill="none" stroke="#fff" stroke-width="1.2"/></svg></div>
  </div>

  <div class="abs map" role="img" aria-label="Road map of the area around the clinic with a marker at its location"></div>

  <h2 class="abs h2 form-title">Send us a Message</h2>
  <div class="abs input f1">First Name <i>*</i></div>
  <div class="abs input f2">Last Name <i>*</i></div>
  <div class="abs input f3">Phone Number <i>*</i></div>
  <div class="abs input f4">E-mail <i>*</i></div>
  <div class="abs input f5">Write your Message</div>
  <a class="abs send" href="#">Send <svg width="5" height="8" viewBox="0 0 5 8"><path d="M1 1l3 3-3 3" fill="none" stroke="#fff" stroke-width="1.3"/></svg></a>

  <h2 class="abs h2 contact-title">Contact</h2>
  <ul class="abs contact-list">
    <li><svg width="8" height="11" viewBox="0 0 8 11"><path d="M4 0a4 4 0 0 0-4 4c0 3 4 7 4 7s4-4 4-7a4 4 0 0 0-4-4z" fill="#bbb"/><circle cx="4" cy="4" r="1.5" fill="#fff"/></svg><span>&nbsp;Harbor Clinic, 48 Linden Avenue,<br>Brookvale, NY 10160, USA</span></li>
    <li><svg width="10" height="10" viewBox="0 0 10 10"><path d="M2 0l2 2.5-1 1.2a6 6 0 0 0 3.3 3.3l1.2-1L10 8l-1.5 2C4 10 0 6 0 1.5z" fill="#bbb"/></svg><span>Phone: <b>+123 480 210</b></span></li>
    <li><svg width="11" height="10" viewBox="0 0 11 10"><rect x="2.5" y="0" width="6" height="3" fill="#bbb"/><rect x="0" y="3" width="11" height="5" rx="1" fill="#bbb"/><rect x="2.5" y="6" width="6" height="4" fill="#fff" stroke="#bbb"/></svg><span>Fax: <b>+123 480 211</b></span></li>
    <li><svg width="11" height="8" viewBox="0 0 11 8"><rect width="11" height="8" fill="#bbb"/><path d="M0 0l5.5 4.5L11 0" fill="none" stroke="#fff"/></svg><span>Email: <a href="#">hello@clinicmail.com</a></span></li>
    <li><svg width="11" height="11" viewBox="0 0 11 11"><circle cx="5.5" cy="5.5" r="5" fill="#bbb"/><path d="M5.5 2.5v3.2l2 1.3" fill="none" stroke="#fff" stroke-width="1.1"/></svg><span>Hours: <b>Mon – Fri 8:00 – 17:00</b><br>Sat 9:00 – 13:00, Sun closed</span></li>
  </ul>

  <footer class="abs footer">
    <div class="abs brand"><span class="dot"></span>Medical</div>
    <p class="abs about">Lorem ipsum dolor sit amet, teft consecte tur adipiscing.</p>
    <div class="abs f-contact">
      <div class="f-row"><svg width="8" height="11" viewBox="0 0 8 11"><path d="M4 0a4 4 0 0 0-4 4c0 3 4 7 4 7s4-4 4-7a4 4 0 0 0-4-4z" fill="#ddd"/><circle cx="4" cy="4" r="1.5" fill="#333436"/></svg><span>&nbsp;Harbor Clinic<br>48 Linden Avenue<br>Brookvale, NY 10160</span></div>
      <div class="f-row" style="margin-bottom:0"><svg width="10" height="28" viewBox="0 0 10 28"><path d="M2 1l2 2.5-1 1.2a6 6 0 0 0 3.3 3.3l1.2-1L10 9l-1.5 2C4 11 0 7 0 2.5z" fill="#ddd"/><rect x="2" y="16" width="6" height="3" fill="#ddd"/><rect x="0" y="19" width="10" height="4" fill="#ddd"/><rect x="2" y="22" width="6" height="3" fill="#333436" stroke="#ddd"/></svg><span>+123 480 210<br>+123 480 211</span></div>
      <div class="f-row" style="margin-top:12px"><svg width="10" height="15" viewBox="0 0 10 15"><rect y="5" width="10" height="7" fill="#ddd"/><path d="M0 5l5 4 5-4" fill="none" stroke="#333436"/></svg><b>hello@clinicmail.com</b></div>
    </div>

    <div class="f-col clinic-links">
      <h4>OUR CLINIC</h4>
      <ul>
        <li><svg width="5" height="7" viewBox="0 0 5 7"><path d="M1 1l2.5 2.5L1 6" fill="none" stroke="#fff"/></svg>Mission</li>
        <li><svg width="5" height="7" viewBox="0 0 5 7"><path d="M1 1l2.5 2.5L1 6" fill="none" stroke="#fff"/></svg>Services</li>
        <li><svg width="5" height="7" viewBox="0 0 5 7"><path d="M1 1l2.5 2.5L1 6" fill="none" stroke="#fff"/></svg>Schedules</li>
        <li><svg width="5" height="7" viewBox="0 0 5 7"><path d="M1 1l2.5 2.5L1 6" fill="none" stroke="#fff"/></svg>Policies</li>
        <li><svg width="5" height="7" viewBox="0 0 5 7"><path d="M1 1l2.5 2.5L1 6" fill="none" stroke="#fff"/></svg>More</li>
      </ul>
    </div>

    <div class="f-col resources">
      <h4>RESOURCES</h4>
      <div class="res-item"><span>›</span><p>Integer iaculis egestas odio, vel dictum turpis placerat id. Pellentesque semper nisl eget: <b>t.co/xYq7Lmn</b><span class="ago">2 days ago</span></p></div>
      <div class="res-item"><span>›</span><p>Curabitur consequat tortor ut eros posu ere rutrum donec metus nisl, dictum vita fermentum: <b>t.co/xYq7Lmn</b><span class="ago">6 days ago</span></p></div>
    </div>

    <div class="f-col news">
      <h4 style="margin-bottom:16px">NEWSLETTER</h4>
      <p>Ipsum dolor sit amet, teft consecte tur adipiscing elit ut eunt.</p>
      <div class="subscribe"><div class="field">Email Address</div><div class="btn">Subscribe</div></div>
    </div>
  </footer>

  <div class="abs footer-bottom">Copyright 2015 Medical | All Rights Reserved</div>
</div>
</body>
</html>
```